Communication and Marketing agency needs a new presentation card

We are a group of communication and marketing agencies specialized in companies that are in the logistics and industrial sector. The head agency is TELVANO Grupo and the group consists of 4 agencies: TELVANO Media, TELVANO Digital, TELVANO Research and DifundeEnPantalla. We hace 4 offices in Spain (Madrid, Barcelona, Valencia and Murcia). We are looking for a clean and attractive design that transmits our experience, brand presence in the market and knowledge to those who receive the card.It has to maintain the colors of the logo that is attached.
Target Market(s)
logistics and industrial sector
Marketing department
Contact Information for Business Card
Clean and attractive design

```html
<!DOCTYPE html>
<html lang="en">
<head>
<meta charset="utf-8">
<title>TELVANO Grupo – Business Card</title>
<link rel="stylesheet" href="https://fonts.googleapis.com/css2?family=Open+Sans:wght@400;600&family=Oswald:wght@500&display=swap">
<style>
  :root {
    --backdrop: #7b7c82;
    --paper: #f1f1f1;
    --paper-shade: #e6e6e6;
    --brand-red: #b01e28;
    --brand-red-deep: #8c1a22;
    --ink: #444446;
    --ink-light: #e2e2e2;
  }
  * { margin: 0; padding: 0; box-sizing: border-box; }
  html, body {
    width: 1200px; height: 1144px; overflow: hidden;
    background: var(--backdrop);
    font-family: "Open Sans", Arial, sans-serif;
  }
  .card {
    position: absolute;
    left: 255px;
    width: 690px; height: 394px;
    box-shadow: -6px 14px 28px rgba(0,0,0,0.45);
  }
  /* Front */
  .card--front {
    top: 149px;
    background: linear-gradient(135deg, #f7f7f7 0%, var(--paper) 45%, var(--paper-shade) 100%);
  }
  .brand {
    position: absolute;
    left: 28px; top: 44px;
    color: var(--brand-red);
    font-weight: 400;
    font-size: 34px;
    line-height: 1;
    letter-spacing: 1px;
  }
  .person {
    position: absolute;
    right: 27px; top: 190px;
    text-align: right;
  }
  .person__name {
    font-family: "Oswald", Arial, sans-serif;
    font-weight: 500;
    font-size: 28px;
    line-height: 1.1;
    letter-spacing: 1px;
    color: var(--brand-red);
  }
  .person__role {
    font-size: 18px;
    line-height: 1.1;
    color: var(--ink);
  }
  .divider {
    position: absolute;
    left: 28px; right: 27px; top: 264px;
    height: 1px; background: var(--brand-red);
  }
  .address {
    position: absolute;
    left: 28px; top: 307px;
    font-size: 16px; line-height: 22px;
    color: var(--ink);
  }
  .contacts {
    position: absolute;
    right: 27px; top: 286px;
    list-style: none;
    text-align: right;
    font-size: 16px; line-height: 21px;
    color: var(--ink);
  }
  .contacts li { display: flex; justify-content: flex-end; align-items: center; gap: 7px; }
  .contacts svg { width: 13px; height: 13px; fill: var(--brand-red); }
  /* Back */
  .card--back {
    top: 602px;
    background: linear-gradient(135deg, var(--brand-red) 0%, #9c1b25 50%, var(--brand-red-deep) 100%);
  }
  .brand--hero {
    left: 0; right: 0; top: 128px;
    text-align: center;
    color: var(--ink-light);
    font-size: 60px;
    letter-spacing: 2px;
  }
  .agencies {
    position: absolute;
    left: 0; right: 0; top: 318px;
    display: flex; justify-content: center; gap: 34px;
    list-style: none;
    color: var(--ink-light);
    font-size: 15px;
    letter-spacing: 0.5px;
  }
</style>
</head>
<body>
  <section class="card card--front">
    <div class="brand">TELVANO Grupo</div>
    <div class="person">
      <div class="person__name">MARTINA CORTÉS</div>
      <div class="person__role">Founder</div>
    </div>
    <div class="divider"></div>
    <address class="address" style="font-style:normal">
      210-240 Calle Lirio<br>
      MD 28014, Spain
    </address>
    <ul class="contacts">
      <li>(000) 987-321-00
        <svg viewBox="0 0 16 16" aria-hidden="true"><path d="M3.6 1.5l2.3 2.6-1.3 2a9 9 0 0 0 5.3 5.3l2-1.3 2.6 2.3-1.6 2.1C7.4 15.4.6 8.6 1.5 3.1z"/></svg>
      </li>
      <li>info@telvanogroup.com
        <svg viewBox="0 0 16 16" aria-hidden="true"><path d="M1 3h14v1.5L8 9 1 4.5zM1 6.3l7 4.4 7-4.4V13H1z"/></svg>
      </li>
      <li>www.telvanogroup.com
        <svg viewBox="0 0 16 16" aria-hidden="true"><circle cx="8" cy="8" r="7"/><path d="M5 4h3l1 2-2 2 1 3-2 1-1-3-2-1z" fill="#fff"/></svg>
      </li>
    </ul>
  </section>

  <section class="card card--back">
    <div class="brand brand--hero">TELVANO Grupo</div>
    <ul class="agencies">
      <li>TELVANO Research</li>
      <li>TELVANO Media</li>
      <li>TELVANO Digital</li>
    </ul>
  </section>
</body>
</html>
```